Brightfield Ventures Inc. Letterhead

Creation of attractive and eye catching letterhead for a business start-up for the construction industry. Letterhead must relate to construction, but avoid standard hammer and tools in the design.

I forgot to add some details, sorry about that. Some pertinent info: Ph: 916-555-0187 brightfieldventures.example 448 Willowmere Ave, Ste 210 Folsom, CA 95999 info@brightfieldventures.example not sure if slogan should be in there" “Connecting construction professionals to create a purpose driven industry.” must be able to be used in word. Thanks!

```html
<!DOCTYPE html>
<html lang="en">
<head>
<meta charset="utf-8">
<title>Brightfield Ventures Inc. Letterhead</title>
<link href="https://fonts.googleapis.com/css2?family=Montserrat:wght@600&family=Open+Sans:wght@400;700&display=swap" rel="stylesheet">
<style>
  :root {
    --brand-red: #c0080b;
    --brand-navy: #13185a;
    --ink: #3a3a3a;
    --paper: #fbfbfb;
    --backdrop: #e9e9eb;
  }
  * { box-sizing: border-box; margin: 0; padding: 0; }
  html, body { width: 1200px; height: 784px; overflow: hidden; }
  body {
    background: var(--backdrop);
    display: flex; align-items: center; justify-content: center;
    font-family: "Open Sans", Arial, sans-serif;
    color: var(--ink);
  }
  .letterhead {
    position: relative;
    width: 580px; height: 750px;
    background: var(--paper);
    box-shadow: 0 6px 22px rgba(0,0,0,.12);
    overflow: hidden;
  }
  .swoosh { position: absolute; top: 0; left: 0; width: 580px; height: 210px; }
  .brand {
    position: absolute; left: 30px; top: 40px;
    display: flex; align-items: center; gap: 7px;
    font-family: "Montserrat", Arial, sans-serif; font-weight: 600;
    font-size: 13px; letter-spacing: .05em; text-transform: uppercase;
    color: var(--brand-navy); white-space: nowrap;
  }
  .brand-mark { width: 12px; height: 12px; background: var(--brand-red); }
  .contact {
    position: absolute; left: 420px; top: 40px;
    list-style: none; font-size: 8px; line-height: 13px; color: var(--ink);
    white-space: nowrap;
  }
  .contact li { display: flex; align-items: flex-start; gap: 5px; }
  .contact svg { width: 8px; height: 8px; margin-top: 2.5px; flex: none; fill: var(--brand-red); }
  .letter { position: absolute; left: 92px; top: 236px; width: 400px; }
  .salutation { font-weight: 700; font-size: 13px; margin-bottom: 14px; }
  .letter p { font-size: 10.5px; line-height: 15.5px; margin-bottom: 14px; }
  .signature {
    width: 120px; height: 54px; margin-top: 10px;
    background: linear-gradient(90deg, #e6e6e6, #f3f3f3);
    border-radius: 4px;
  }
</style>
</head>
<body>
  <main class="letterhead">
    <svg class="swoosh" viewBox="0 0 580 210" aria-hidden="true">
      <path fill="var(--brand-navy)" d="M470,0 C360,50 220,135 0,158 L0,150 C150,150 260,110 330,0 Z"/>
      <path fill="var(--brand-red)" d="M330,0 L380,0 C290,120 150,180 0,195 L0,150 C150,150 260,110 330,0 Z"/>
    </svg>

    <div class="brand"><span class="brand-mark"></span>Brightfield Ventures</div>

    <ul class="contact">
      <li><svg viewBox="0 0 10 10"><path d="M2 0h2l1 3-1.5 1a6 6 0 0 0 2.5 2.5L7 5l3 1v2a2 2 0 0 1-2 2A8 8 0 0 1 0 2a2 2 0 0 1 2-2z"/></svg>916-555-0187</li>
      <li><svg viewBox="0 0 10 10"><path d="M0 2h10v6H0z"/></svg>info@brightfieldventures.example</li>
      <li><svg viewBox="0 0 10 10"><circle cx="5" cy="5" r="5"/></svg>brightfieldventures.example</li>
      <li><svg viewBox="0 0 10 10"><path d="M5 0a3.5 3.5 0 0 1 3.5 3.5C8.5 6 5 10 5 10S1.5 6 1.5 3.5A3.5 3.5 0 0 1 5 0z"/></svg>448 Willowmere Ave, Ste 210<br>Folsom, CA 95999</li>
    </ul>

    <section class="letter">
      <h1 class="salutation">Dear Mr. Hale,</h1>
      <p>Lorem Ipsum is simply dummy text of the printing and typesetting industry. Lorem Ipsum has been the industry's standard dummy text ever since the 1500s, when an unknown printer took a galley of type and scrambled it to make a type specimen book. It has survived not only five centuries, but also the leap into electronic typesetting, remaining essentially unchanged.</p>
      <p>The standard chunk of Lorem Ipsum used since the 1500s is reproduced below for those interested. Sections 1.10.32 and 1.10.33 from "de Finibus Bonorum et Malorum" by Aurelian are also reproduced in their exact original form, accompanied by English versions from the 1914 translation by H. Marlowe.</p>
      <p>Lorem Ipsum is simply dummy text of the printing and typesetting industry. Lorem Ipsum has been the industry's standard dummy text ever since the 1500s, when an unknown printer took a galley of type and scrambled it to make a type specimen book. It has survived not only five centuries, but also the leap into electronic typesetting, remaining essentially unchanged. It was popularised in the</p>
      <div class="signature" role="img" aria-label="Handwritten signature of the sender"></div>
    </section>
  </main>
</body>
</html>
```